Fresh Dwelling Tract Guide needs a new Landing Page

I like to get a landing page or website with 2-3 pages to help target home buyers who are looking to buy homes from builders such as TW Residences, Morvik, P.L. Fennick, etc. The landing page/website to be non-cluttered and be able to explain to home buyers that there are many benefits to include me as their buyer's agent when they buy a brand new home from any builders.
I may want to incorporate a short explanation video (animated) on the landing page and then for the viewer to click on a button that will take them to another page where they can search for new homes from different builders.
Target Market(s)
Home buyers looking to buy brand new home from builders such as TW Residences, Morvik, P.L. Fennick, etc.
Industry/Entity Type
Real Estate
Number of Pages Required
2 page
Font styles to use
Requirements
Must have
- The landing page may have the explanation video at the bottom of the landing page (scrolled down) or there may be a CALL TO ACTION button that takes the viewer to the 2nd page to watch the explanation video. Once they watched the explanation video and are still interested, they can click on another CALL TO ACTION button that will take them to another website that they will be able to search for all the available new homes and register their contact information.
Should not have
- No clutters and no dark colors.

```html
<!DOCTYPE html>
<html lang="en">
<head>
<meta charset="utf-8">
<title>Fresh Dwelling Tract Guide</title>
<link rel="stylesheet" href="https://fonts.googleapis.com/css2?family=Open+Sans:wght@400;500&display=swap">
<style>
  :root {
    --brand-green: #8abf6e;
    --heading-green: #3b7d2f;
    --ink: #111111;
    --paper: #ffffff;
    --stone: #9b7a52;
    --sky: #c9d3dc;
    --foliage: #4f7a34;
  }
  * { margin: 0; padding: 0; box-sizing: border-box; }
  html, body { width: 919px; height: 1200px; overflow: hidden; }
  body {
    position: relative;
    background: var(--paper);
    font-family: "Open Sans", Arial, sans-serif;
    color: var(--ink);
  }
  .hero {
    position: absolute; left: 0; top: 0; width: 919px; height: 610px;
    background:
      radial-gradient(ellipse 120px 260px at 460px 180px, var(--sky) 0%, rgba(201,211,220,0) 100%),
      linear-gradient(90deg, #8a6a44 0%, var(--stone) 30%, #a88a62 45%, #7d6a4a 58%, var(--foliage) 78%, #3f6a2a 100%);
  }
  .hero::after {
    content: ""; position: absolute; left: 0; right: 0; bottom: 0; height: 200px;
    background: linear-gradient(180deg, rgba(70,100,50,0) 0%, rgba(70,100,50,0.55) 100%);
  }
  .brand-tab {
    position: absolute; left: 385px; top: 0; width: 146px; height: 75px;
    background: var(--brand-green);
    display: flex; align-items: center; justify-content: center; text-align: center;
    font-size: 10.5px; line-height: 14px; text-transform: uppercase; color: var(--ink);
    padding: 0 8px; z-index: 2;
  }
  .play-button { position: absolute; left: 435px; top: 280px; z-index: 2; }
  .intro-heading {
    position: absolute; left: 34px; top: 670px;
    font-size: 16px; font-weight: 500; color: var(--heading-green);
  }
  .intro-text {
    position: absolute; top: 724px; width: 410px;
    font-size: 17px; line-height: 21px;
  }
  .intro-text--left { left: 34px; }
  .intro-text--right { left: 480px; }
  .button {
    position: absolute; left: 330px; width: 258px; height: 53px;
    display: flex; align-items: center; justify-content: center;
    font-size: 16px; text-transform: uppercase; background: transparent;
  }
  .button--search { top: 853px; border: 2px solid var(--brand-green); color: var(--heading-green); }
  .contact-band {
    position: absolute; left: 0; top: 958px; width: 919px; height: 242px;
    background: var(--brand-green);
  }
  .contact-band__tagline {
    position: absolute; left: 0; width: 919px; top: 32px; text-align: center; font-size: 17.5px;
  }
  .button--contact { top: 85px; border: 2px solid var(--ink); color: var(--ink); }
  .footer-rights {
    position: absolute; left: 21px; top: 190px; font-size: 11px; text-transform: uppercase;
  }
  .footer-rights span { text-transform: none; }
  .social-links { position: absolute; left: 771px; top: 176px; }
</style>
</head>
<body>
  <section class="hero" role="img" aria-label="Photo of a narrow cobblestone village lane between old stone houses with potted plants, flowers and ivy under a cloudy blue sky"></section>
  <div class="brand-tab">Fresh Dwelling Tract Guide</div>
  <svg class="play-button" width="50" height="50" viewBox="0 0 50 50" aria-label="Play video">
    <circle cx="25" cy="25" r="23.5" fill="none" stroke="#111" stroke-width="2"/>
    <path d="M19 15 L35 25 L19 35 Z" fill="none" stroke="#111" stroke-width="2" stroke-linejoin="round"/>
  </svg>

  <h2 class="intro-heading">Get to know us:</h2>
  <p class="intro-text intro-text--left">Lorem ipsum dolor sit amet, consectetur adipiscing elit. Sed id aliquam ligula. Morbi eget ornare nisi. Curabitur vel quam id urna aliquet facilisis.</p>
  <p class="intro-text intro-text--right">Nullam blandit pharetra mi sit amet finibus. Sed est enim, dignissim eget dapibus vel, aliquam eu ipsum.</p>
  <a class="button button--search">Search</a>

  <footer class="contact-band">
    <p class="contact-band__tagline">Lorem ipsum dolor sit amet, consectetur adipiscing elit.</p>
    <a class="button button--contact">Contact Us</a>
    <p class="footer-rights">Fresh Dwelling Tract Guide 2018 <span>Rights</span></p>
    <svg class="social-links" width="120" height="30" viewBox="0 0 120 30" aria-label="Social media links">
      <circle cx="16" cy="15" r="13.5" fill="#111" stroke="#111" stroke-width="1"/>
      <circle cx="60" cy="15" r="13.5" fill="#111" stroke="#111" stroke-width="1"/>
      <circle cx="104" cy="15" r="13.5" fill="#111" stroke="#111" stroke-width="1"/>
    </svg>
  </footer>
</body>
</html>
```